Professional violinist needs business cards

I am trying to attract the following jobs:
-private violin lessons (primarily classical)
-performance gigs (weddings, birthday parties, funerals, etc.)
-collaborations with other artists (studio recordings, performances)

I want to communicate that I have a very high standard of excellence for my work, but I also love people and celebrations.
Values/style words I like are:
love, joy, peace, fun, beauty, authenticity, excellence, warmth, refined/sleek, free spirited. If that's too confusing, just ignore :)

I will attach my favorite business card template that I could find on Canva. The lines are supposed to be like a music staff, which I think is really cool, but I also don't want it to look too busy. I like the simple black and white--I think it looks sharp--but I also am open to other ideas. I also have seen business cards with pictures included that looked great, so I attached an image that could be used as well.

I am also attaching a file that I made of my initials that could be used as a logo, but I'm not sure if it should be included.

Information on the card:
-My name (18 letters total)
-"violinist"
-phone number, email, website

Thank you!

```html
<!DOCTYPE html>
<html lang="en">
<head>
<meta charset="utf-8">
<title>Coralie Wintersand — Violinist Business Card</title>
<link rel="stylesheet" href="https://fonts.googleapis.com/css2?family=Dancing+Script:wght@600&family=Cinzel:wght@500&family=Alegreya:wght@400&display=swap">
<style>
  :root {
    --backdrop: #1b1c1e;
    --card-dark: #23282b;
    --card-ink: #f4f1ea;
    --contact-ink: #e6e3dc;
    --accent-gold: #d7c9a6;
    --photo-stone: #6e665a;
    --photo-shadow: #2a2826;
    --photo-gown: #15171a;
  }
  * { box-sizing: border-box; margin: 0; padding: 0; }
  html, body {
    width: 1200px; height: 1108px; overflow: hidden;
    background: var(--backdrop);
  }
  .stage {
    position: relative; width: 1200px; height: 1108px;
    display: flex; justify-content: center; align-items: center; gap: 60px;
  }
  .card {
    position: relative; width: 420px; height: 690px;
    border-radius: 40px; overflow: hidden;
    background: var(--card-dark); color: var(--card-ink);
    box-shadow: 0 18px 40px rgba(0,0,0,.55);
  }
  /* Front */
  .card-photo {
    position: absolute; inset: 0;
    background:
      linear-gradient(180deg, rgba(0,0,0,0) 55%, var(--card-dark) 92%),
      radial-gradient(ellipse 24% 60% at 52% 62%, var(--photo-gown) 0 55%, transparent 85%),
      linear-gradient(135deg, #7a7164 0%, var(--photo-stone) 45%, var(--photo-shadow) 100%);
  }
  .front-brand {
    position: absolute; left: 0; right: 0; top: 470px;
    display: flex; flex-direction: column; align-items: center;
  }
  .brand-mark {
    display: flex; align-items: center; gap: 10px;
    font-family: "Cinzel", serif; font-weight: 500; font-size: 15px;
    letter-spacing: .12em; text-transform: uppercase; white-space: nowrap;
  }
  .brand-mark .dot {
    width: 9px; height: 9px; border-radius: 50%; background: currentColor;
  }
  .person-name {
    font-family: "Dancing Script", cursive; font-weight: 600;
    font-size: 44px; line-height: 1.1; margin-top: 28px; white-space: nowrap;
  }
  .role {
    font-family: "Cinzel", serif; font-weight: 500;
    font-size: 17px; letter-spacing: .28em;
  }
  .role-ruled {
    display: flex; align-items: center; gap: 16px; margin-top: 4px;
  }
  .role-ruled::before, .role-ruled::after {
    content: ""; width: 70px; height: 1.5px; background: var(--card-ink);
  }
  /* Back */
  .back-brand {
    position: absolute; left: 50px; top: 120px;
  }
  .back-brand .brand-mark { color: var(--accent-gold); }
  .back-brand .person-name { font-size: 40px; margin-top: 34px; }
  .back-brand .role { margin-top: 2px; }
  .contact {
    position: absolute; left: 50px; bottom: 110px;
    list-style: none; color: var(--contact-ink);
    font-family: "Alegreya", serif; font-size: 20px; line-height: 1.3;
    white-space: nowrap;
  }
  .contact .highlight { color: var(--accent-gold); }
</style>
</head>
<body>
<main class="stage">
  <section class="card card-front">
    <div class="card-photo" role="img" aria-label="Portrait photograph of the violinist in a black gown holding a violin on stone stairs"></div>
    <div class="front-brand">
      <div class="brand-mark"><span class="dot"></span>Coralie Wintersand</div>
      <div class="person-name">Coralie Wintersand</div>
      <div class="role role-ruled">VIOLINIST</div>
    </div>
  </section>

  <section class="card card-back">
    <div class="back-brand">
      <div class="brand-mark"><span class="dot"></span>Coralie Wintersand</div>
      <div class="person-name">Coralie Wintersand</div>
      <div class="role">VIOLINIST</div>
    </div>
    <ul class="contact">
      <li>+1 (555) 014-2368</li>
      <li>Coralie@CoralieWintersand.com</li>
      <li>www.<span class="highlight">CoralieWintersand</span>.com</li>
      <li>Portland, OR</li>
    </ul>
  </section>
</main>
</body>
</html>
```